Business Card Design

New business card design

Target Market(s)

Residential & Commercial Property Managers

Industry/Entity Type

Plumbing Services

Contact Information for Business Card

Name - Rowan Keddle, title - Director, Phone Number - 0431 286 517, email - rowan@tbk-plumbing.com.au, Company ABN - 73 215 904 386,

Font styles to use
Sans Serif

Colors
0054AA
0677BA
7BADD7
CADEEF
E8F1F8

```html
<!DOCTYPE html>
<html lang="en">
<head>
<meta charset="utf-8">
<title>TBK Plumbing Services – Business Card</title>
<link rel="stylesheet" href="https://fonts.googleapis.com/css2?family=Michroma&family=Poppins:wght@400;600&display=swap">
<style>
  :root {
    --stage: #9a9a9a;
    --navy: #032b41;
    --sky: #63c6ee;
    --cyan: #00d6f2;
    --brand-blue: #1089c6;
    --ink: #111111;
    --white: #ffffff;
    --photo-top: #8fc1e4;
    --photo-mid: #3d6f9c;
    --photo-low: #1c3550;
  }
  * { margin: 0; padding: 0; box-sizing: border-box; }
  html, body { width: 1200px; height: 1031px; overflow: hidden; background: var(--stage); }
  .stage { position: relative; width: 1200px; height: 1031px; }
  .card {
    position: absolute; top: 94px; width: 487px; height: 853px;
    box-shadow: 0 10px 22px rgba(0,0,0,.35);
  }
  .card--front { left: 83px; }
  .card--back { left: 627px; }
  .card svg { display: block; width: 100%; height: 100%; }
  .wordmark { font-family: "Poppins", sans-serif; font-weight: 600; fill: var(--white); }
  .abn-label, .abn-number { font-family: "Poppins", sans-serif; font-weight: 400; }
  .abn-label { fill: var(--navy); }
  .abn-number { fill: var(--white); }
  .person-name { font-family: "Michroma", sans-serif; fill: var(--brand-blue); }
  .person-role { font-family: "Poppins", sans-serif; font-weight: 400; fill: var(--ink); }
  .contact-phone { font-family: "Poppins", sans-serif; font-weight: 600; fill: var(--ink); }
  .contact-line { font-family: "Poppins", sans-serif; font-weight: 400; fill: var(--ink); }
</style>
</head>
<body>
<div class="stage">

  <!-- Front of card -->
  <div class="card card--front">
    <svg viewBox="0 0 812 1421" xmlns="http://www.w3.org/2000/svg">
      <defs>
        <linearGradient id="bandGrad" x1="0" y1="0" x2="1" y2="0">
          <stop offset="0" stop-color="var(--sky)"/>
          <stop offset="1" stop-color="var(--cyan)"/>
        </linearGradient>
        <linearGradient id="cityGrad" x1="0" y1="0" x2="0" y2="1">
          <stop offset="0" stop-color="var(--photo-top)"/>
          <stop offset="0.45" stop-color="var(--photo-mid)"/>
          <stop offset="1" stop-color="var(--photo-low)"/>
        </linearGradient>
      </defs>
      <rect class="card-base" width="812" height="1421" fill="var(--navy)"/>
      <text class="wordmark" x="406" y="372" font-size="72" text-anchor="middle">TBK Plumbing</text>
      <text class="wordmark" x="406" y="432" font-size="30" text-anchor="middle" letter-spacing="12">SERVICES</text>
      <polygon class="city-photo" role="img" aria-label="Photo of a modern city skyline with glass towers"
               points="0,598 475,777 475,735 812,858 812,1421 0,1421" fill="url(#cityGrad)"/>
      <polygon class="accent-band" points="0,536 475,720 475,777 0,598" fill="url(#bandGrad)"/>
      <polygon class="accent-band" points="475,655 812,780 812,842 475,718" fill="url(#bandGrad)"/>
    </svg>
  </div>

  <!-- Back of card -->
  <div class="card card--back">
    <svg viewBox="0 0 812 1421" xmlns="http://www.w3.org/2000/svg">
      <defs>
        <linearGradient id="bandGrad2" x1="0" y1="0" x2="1" y2="0">
          <stop offset="0" stop-color="var(--sky)"/>
          <stop offset="1" stop-color="var(--cyan)"/>
        </linearGradient>
        <linearGradient id="ruleGrad" x1="0" y1="0" x2="1" y2="0">
          <stop offset="0" stop-color="var(--cyan)" stop-opacity="0"/>
          <stop offset="0.5" stop-color="var(--cyan)"/>
          <stop offset="1" stop-color="var(--cyan)" stop-opacity="0"/>
        </linearGradient>
      </defs>
      <rect class="card-base" width="812" height="1421" fill="var(--navy)"/>
      <text class="wordmark" x="406" y="322" font-size="72" text-anchor="middle">TBK Plumbing</text>
      <text class="wordmark" x="406" y="382" font-size="30" text-anchor="middle" letter-spacing="12">SERVICES</text>

      <g class="abn-badge">
        <rect x="206" y="455" width="381" height="45" rx="6" fill="none" stroke="var(--sky)" stroke-width="3"/>
        <path d="M212,455 H324 V500 H212 a6,6 0 0 1 -6,-6 V461 a6,6 0 0 1 6,-6 Z" fill="var(--sky)"/>
        <text class="abn-label" x="265" y="490" font-size="31" text-anchor="middle">ABN</text>
        <text class="abn-number" x="455" y="491" font-size="32" text-anchor="middle">73 215 904 386</text>
      </g>

      <polygon class="info-panel" points="0,600 475,777 475,735 812,858 812,1421 0,1421" fill="var(--white)"/>
      <polygon class="accent-band" points="0,536 475,720 475,777 0,598" fill="url(#bandGrad2)"/>
      <polygon class="accent-band" points="475,655 812,780 812,842 475,718" fill="url(#bandGrad2)"/>

      <text class="person-name" x="406" y="899" font-size="54" text-anchor="middle" textLength="566" lengthAdjust="spacingAndGlyphs">ROWAN KEDDLE</text>
      <text class="person-role" x="406" y="948" font-size="44" text-anchor="middle">Director</text>
      <rect class="rule" x="150" y="966" width="512" height="4" fill="url(#ruleGrad)"/>

      <g class="contact-icons" fill="var(--brand-blue)">
        <rect x="292" y="1022" width="48" height="50" rx="6"/>
        <path d="M305,1036 q4,-4 7,0 l4,6 q1,3 -2,5 l-2,1 q3,7 10,10 l1,-2 q2,-3 5,-2 l6,4 q3,3 0,6 l-3,3 q-6,3 -17,-5 q-11,-9 -12,-19 Z" fill="var(--white)"/>
        <rect x="379" y="1022" width="50" height="50" rx="6"/>
        <g fill="none" stroke="var(--white)" stroke-width="3">
          <rect x="391" y="1036" width="26" height="20" rx="2"/>
          <path d="M391,1037 L404,1048 L417,1037 M391,1055 L400,1046 M417,1055 L408,1046"/>
        </g>
        <rect x="467" y="1022" width="50" height="50" rx="6"/>
        <g fill="none" stroke="var(--white)" stroke-width="2.5">
          <circle cx="492" cy="1047" r="14"/>
          <ellipse cx="492" cy="1047" rx="6" ry="14"/>
          <path d="M478,1047 H506 M481,1039 H503 M481,1055 H503 M492,1033 V1061"/>
        </g>
      </g>

      <text class="contact-phone" x="406" y="1151" font-size="46" text-anchor="middle">0431 286 517</text>
      <text class="contact-line" x="406" y="1216" font-size="34" text-anchor="middle">rowan@tbk-plumbing.com.au</text>
      <text class="contact-line" x="406" y="1280" font-size="34" text-anchor="middle">www.tbk-plumbing.com.au</text>
    </svg>
  </div>

</div>
</body>
</html>
```